BLS Business Card 2018

Larkmere Chiropractic. We have two locations that we want to advertise on the same card. Brightvale OrthoCore campus address: 3815 Pellham Dr., Suite 240, Flowood, MS 39417. Madison address: 246 Willowmere Dr., Building D., Madison, MS 39284. website: www.drlarkmere-example.com. o:(601)555-0147 f:(601)555-0183

Target Market(s)

Health care decision makers: primary care doctors and mothers

Contact Information for Business Card

I have no idea; up for any suggestions and I'd do much better picking from examples versus describing what I'm looking for. We are in a very high end location and would like the cards to look really sharp.

Requirements
Must have
• My name, Martin R Belvane, D.C.

```html
<!DOCTYPE html>
<html lang="en">
<head>
<meta charset="utf-8">
<title>Larkmere Chiropractic Business Card</title>
<link rel="stylesheet" href="https://fonts.googleapis.com/css2?family=Cormorant+Garamond:wght@500;600&family=Open+Sans:wght@400;700&display=swap">
<style>
  :root {
    --backdrop: #2b2b2b;
    --card-light: #f4f4f4;
    --card-dark: #020202;
    --ink: #111111;
    --ink-soft: #555555;
    --ink-reverse: #e8e8e8;
    --art-light-a: #f4f4f4;
    --art-light-b: #dcdcdc;
    --art-dark-a: #3a3a3a;
    --art-dark-b: #020202;
  }
  * { margin: 0; padding: 0; box-sizing: border-box; }
  html, body {
    width: 1200px;
    height: 960px;
    overflow: hidden;
    background: var(--backdrop);
  }
  .canvas {
    position: relative;
    width: 1200px;
    height: 960px;
  }
  .card {
    position: absolute;
    box-shadow: 0 3px 8px rgba(0,0,0,0.45);
  }
  .card-front {
    left: 322px;
    top: 108px;
    width: 598px;
    height: 342px;
    background: var(--card-light);
    color: var(--ink);
  }
  .card-back {
    left: 320px;
    top: 494px;
    width: 600px;
    height: 340px;
    background: var(--card-dark);
  }
  .brand-name {
    position: absolute;
    left: 26px;
    top: 32px;
    font-family: "Cormorant Garamond", serif;
    font-weight: 600;
    font-size: 43px;
    line-height: 1;
    letter-spacing: 0.5px;
  }
  .brand-tagline {
    position: absolute;
    left: 27px;
    top: 74px;
    font-family: "Cormorant Garamond", serif;
    font-weight: 500;
    font-size: 27px;
    line-height: 1;
    font-variant: small-caps;
    letter-spacing: 1.5px;
  }
  .details {
    position: absolute;
    z-index: 2;
    left: 27px;
    top: 128px;
    font-family: "Open Sans", sans-serif;
    font-size: 14px;
    line-height: 19.5px;
    color: var(--ink-soft);
    white-space: nowrap;
  }
  .practitioner {
    font-family: "Open Sans", sans-serif;
    font-weight: 700;
    font-size: 17px;
    letter-spacing: -0.3px;
    color: var(--ink);
    margin-bottom: 6px;
  }
  .location { margin-bottom: 6px; }
  .figure-art {
    position: absolute;
    z-index: 1;
    right: 4px;
    top: 4px;
    width: 228px;
    height: 336px;
    background: radial-gradient(ellipse at 50% 45%, var(--art-light-b) 0%, var(--art-light-a) 70%);
  }
  .figure-art-dark {
    position: absolute;
    left: 234px;
    top: 82px;
    width: 134px;
    height: 176px;
    background: radial-gradient(ellipse at 50% 50%, var(--art-dark-a) 0%, var(--art-dark-b) 72%);
  }
  .back-url {
    position: absolute;
    left: 0;
    right: 0;
    top: 279px;
    text-align: center;
    font-family: "Open Sans", sans-serif;
    font-size: 14px;
    letter-spacing: 4.5px;
    color: var(--ink-reverse);
  }
</style>
</head>
<body>
<div class="canvas">
  <section class="card card-front">
    <div class="brand-name">LARKMERE</div>
    <div class="brand-tagline">Chiropractic</div>
    <div class="details">
      <div class="practitioner">MARTIN R BELVANE, D.C.</div>
      <div class="location">Brightvale OrthoCore campus :<br>3815 Pellham Dr., Suite 240<br>Flowood, MS 39417.</div>
      <div class="location">Madison address:<br>246 Willowmere Dr., Building D.<br>Madison, MS 39284.</div>
      <div class="contact">P. (601)555-0147<br>F. (601)555-0183 | www.drlarkmere-example.com</div>
    </div>
    <div class="figure-art" role="img" aria-label="Line sketch of a human back and shoulders in motion"></div>
  </section>

  <section class="card card-back">
    <div class="figure-art-dark" role="img" aria-label="Light line sketch of a human back and shoulders on black"></div>
    <div class="back-url">WWW.DRLARKMERE-EXAMPLE.COM</div>
  </section>
</div>
</body>
</html>
```